Flyer for Compassion training days

I need a A5-size, single-sided flyer design for my training days. They are weekends in a blend of Compassionate Communication and Buddhist teachings called Gentlewise Dialogue. The logo for Gentlewise that should be included.
The flyer needs room for 1) course title, 2) course dates, location & price, 3) course description, 4) booking info, 5) my picture & short bio, and 6) the gentlewise.co website (yes, it is 'co' and not 'com).
Updates

Target Market(s)

Women 35-65 years, well-educated, spiritually minded. May have interests like yoga and meditation.

Industry/Entity Type

Health And Wellness

Font styles to use
Sans Serif
Other font styles liked:
• Blue Plaque, Josefina are both great

Colors
fbf289
fdf9cf
cfeae6
33b8a4

Requirements
Must have
• The Gentlewise logo; my picture.
• Elegance. Calm and expansive feel.
• The poster provided in the project files shows you the kind of information I need to include.
• Colours -- greens and yellows, but the options on craft plaza are not quite the right shades.
• The logo colour can be changed.
Nice to have
• Classy (but not cliche) image associated with Buddhism; gentle curves similar to those on the business card (see project files).
Should not have
• Dark background. Busy, loud design. Overly 'swirly' design. Images that I have to buy separately.

```html
<!DOCTYPE html>
<html lang="en">
<head>
<meta charset="utf-8">
<title>Gentlewise Dialogue – Core Course Flyer</title>
<link rel="stylesheet" href="https://fonts.googleapis.com/css2?family=Ubuntu:ital,wght@0,400;0,500;0,700;1,400;1,700&family=Arimo:ital,wght@0,400;0,700;1,400&display=swap">
<style>
  :root {
    --green-deep: #1e9a3c;
    --green-mid: #3cae3f;
    --green-light: #8fd14f;
    --green-title: #2b9c3a;
    --cream: #fdf6da;
    --text-grey: #5a5a5a;
    --white: #ffffff;
    --stone-dark: #5b5b57;
    --stone-mid: #8a8a84;
    --leaf: #7cc44a;
    --photo: #8c8a86;
  }
  * { margin: 0; padding: 0; box-sizing: border-box; }
  html, body { width: 1200px; height: 848px; overflow: hidden; background: var(--cream); }
  .flyer {
    position: relative;
    width: 1200px;
    height: 848px;
    overflow: hidden;
    font-family: "Arimo", Arial, sans-serif;
    color: var(--text-grey);
  }
  .backdrop { position: absolute; inset: 0; }
  .tagline {
    position: absolute;
    top: 20px; left: 0; width: 1200px;
    text-align: center;
    font-family: "Ubuntu", sans-serif;
    font-weight: 700;
    font-size: 39px;
    letter-spacing: 0.6px;
    color: var(--white);
  }
  .brand-tile {
    position: absolute;
    left: 102px; top: 80px;
    width: 118px; height: 116px;
    background: var(--white);
    border-radius: 6px;
    box-shadow: 0 2px 6px rgba(0,0,0,0.25);
    display: flex; flex-direction: column;
    align-items: center; justify-content: center; gap: 8px;
  }
  .brand-mark { width: 22px; height: 22px; background: var(--green-mid); }
  .brand-name {
    font-family: "Arimo", sans-serif;
    font-weight: 700;
    font-size: 17px;
    color: var(--green-mid);
  }
  .course-title {
    position: absolute;
    left: 417px; top: 120px;
    width: 500px;
    text-align: center;
    font-family: "Ubuntu", sans-serif;
    font-weight: 700;
    font-size: 55px;
    line-height: 60px;
    color: var(--green-title);
  }
  .course-bar {
    position: absolute;
    left: 220px; top: 247px;
    width: 956px; height: 58px;
    border: 3px dotted var(--green-mid);
  }
  .course-name {
    position: absolute;
    left: 32px; top: 8px;
    font-family: "Arimo", sans-serif;
    font-style: italic;
    font-weight: 700;
    font-size: 32px;
    line-height: 38px;
    color: var(--green-title);
  }
  .course-details {
    position: absolute;
    right: 6px; top: 0;
    text-align: right;
    font-size: 23px;
    line-height: 26px;
    color: var(--text-grey);
  }
  .column { position: absolute; font-size: 21px; line-height: 28px; }
  .column-left { left: 110px; top: 318px; width: 508px; text-align: justify; }
  .column-right { left: 666px; top: 318px; width: 510px; text-align: justify; }
  .explore-heading {
    margin-top: 22px;
    color: var(--green-title);
    font-weight: 700;
    text-align: left;
  }
  .explore-list { list-style: none; }
  .explore-list li { padding-left: 14px; text-indent: -14px; text-align: left; }
  .booking {
    margin-top: 34px;
    color: var(--green-title);
    font-weight: 700;
    text-align: left;
  }
  .facilitator-photo {
    position: absolute;
    left: 216px; top: 667px;
    width: 112px; height: 141px;
    background: linear-gradient(160deg, #b7b4ae, var(--photo) 60%, #6c6a66);
    border: 2px solid var(--white);
  }
  .facilitator {
    position: absolute;
    left: 345px; top: 670px;
    width: 826px;
    font-size: 20.5px;
    line-height: 28px;
  }
  .facilitator-label { font-weight: 700; }
  .facilitator-bio { font-style: italic; }
  .coaching { margin-top: 20px; font-weight: 700; }
  .stones {
    position: absolute;
    left: 0; top: 640px;
    width: 205px; height: 208px;
    border-radius: 0 110px 0 0;
    background: linear-gradient(200deg, var(--leaf) 0%, var(--stone-mid) 45%, var(--stone-dark) 100%);
  }
  .leaf-glow {
    position: absolute;
    left: 330px; top: 230px;
    width: 560px; height: 420px;
    background: radial-gradient(ellipse at center, rgba(188,214,140,0.3), rgba(253,246,218,0) 70%);
  }
  .site-tile {
    position: absolute;
    left: 927px; top: 757px;
    width: 249px; height: 83px;
    background: var(--white);
    border: 3px solid var(--green-mid);
    border-radius: 8px;
    display: flex; align-items: center; justify-content: center; gap: 12px;
  }
  .site-mark { width: 30px; height: 30px; border-radius: 50%; background: var(--green-mid); }
  .site-name {
    font-family: "Arimo", sans-serif;
    font-weight: 400;
    font-size: 29px;
    color: var(--green-mid);
  }
</style>
</head>
<body>
<main class="flyer">
  <svg class="backdrop" width="1200" height="848" viewBox="0 0 1200 848" aria-hidden="true">
    <defs>
      <radialGradient id="creamGlow" cx="0.5" cy="0.45" r="0.7">
        <stop offset="0" stop-color="#fefbe8"/>
        <stop offset="1" stop-color="#f8eec2"/>
      </radialGradient>
      <linearGradient id="greenBand" x1="0" y1="0" x2="1" y2="0">
        <stop offset="0" stop-color="#1e9a3c"/>
        <stop offset="1" stop-color="#2fa83f"/>
      </linearGradient>
    </defs>
    <rect width="1200" height="848" fill="url(#greenBand)"/>
    <path d="M0,92 Q500,60 900,90 Q1120,110 1200,170 L1200,848 L0,848 Z" fill="url(#creamGlow)"/>
    <path d="M0,92 Q300,70 560,72 Q320,90 60,150 Q20,160 0,175 Z" fill="#8fd14f" opacity="0.9"/>
    <path d="M700,78 Q1000,80 1200,150 L1200,175 Q1050,110 700,78 Z" fill="#8fd14f" opacity="0.8"/>
    <path d="M0,200 Q20,420 130,560 Q40,430 20,240 Z" fill="#8fd14f" opacity="0.55"/>
    <path d="M1200,560 Q1100,740 900,848 L1200,848 Z" fill="#3cae3f" opacity="0.9"/>
    <path d="M1200,520 Q1080,720 860,848 L900,848 Q1100,740 1200,560 Z" fill="#8fd14f" opacity="0.8"/>
  </svg>

  <div class="leaf-glow" role="img" aria-label="Faint decorative leaf motif behind the text"></div>

  <p class="tagline">Mindfulness + Kindness + Compassionate Communication =</p>

  <div class="brand-tile">
    <span class="brand-mark"></span>
    <span class="brand-name">Gentlewise</span>
  </div>

  <h1 class="course-title">Gentlewise Dialogue</h1>

  <div class="course-bar">
    <h2 class="course-name">Core Course</h2>
    <p class="course-details">11-12 Dec • Linden Centre,Edinburgh<br>(£125/100)</p>
  </div>

  <section class="column column-left">
    <p>Gentlewise Dialogue can help you increase awareness &amp; compassion in everyday speech (with yourself &amp; others), better understand your own patterns, and build resilience to challenging situations. Choose from:</p>
    <p class="explore-heading">In this 2-day Core Course, we’ll explore:</p>
    <ul class="explore-list">
      <li>* Compassionate Communication;</li>
      <li>* Buddhist teachings on Right Speech, loving kindness, Right Effort, and more;</li>
      <li>* mindfulness practices;</li>
      <li>* choices available to us in our everyday speech.</li>
    </ul>
  </section>

  <section class="column column-right">
    <p>This workshop will be of interest if you’d like to improve personal and/or professional relationships. Open to all, best suited to those with at least 1 year’s experience with Mindfulness, Buddhism, or Compassionate Communication / NVC.</p>
    <p class="booking">Booking: Book online at TicketNest or write marisol@gentlewise.co</p>
  </section>

  <div class="stones" role="img" aria-label="Stacked zen stones with fresh green leaves"></div>

  <div class="facilitator-photo" role="img" aria-label="Portrait photo of the facilitator"></div>

  <section class="facilitator">
    <p><span class="facilitator-label">Facilitator:</span> <span class="facilitator-bio">Marisol Everhart is an experienced group facilitator, having worked with a range of organisations and presented at a number of festivals &amp; conferences.</span></p>
    <p class="coaching">Marisol offers coaching in Gentlewise Dialogue.</p>
  </section>

  <div class="site-tile">
    <span class="site-mark"></span>
    <span class="site-name">Gentlewise.co</span>
  </div>
</main>
</body>
</html>
```